A website for a Maltese Law Firm

Our law firm needs a website to further its business. The site should have a simple yet effective design. We would need the following sections: About us, Practice Areas, About Malta, Contact. These should be further split as follows:

About us: Our firm, Our values, What others say, Offices

Practice Areas: Crimimal, Citizenship & Residence, Sovereign Patron Pathway, Criminal Defence, Civil Litigation, Arbitration and ADR, Commercial and Corporate, Media Law.

About Malta: just one section.

Contact: Just one section

We would also need a news feed at the front of the site to include latest news regarding our cases.

At the bottom we need a section for our Terms and a Privacy Statement.

Our logo is being attached.

Target Market(s)

All clients looking for legal assistance in Malta

Industry/Entity Type

Legal

Coding

Coded - Design and coding required

Number of Pages Required

1 page

Requirements
Must have
• It must be simple yet striking.

```html
<!DOCTYPE html>
<html lang="en">
<head>
<meta charset="utf-8">
<title>Mercieca &amp; Falzon Advocates</title>
<link rel="stylesheet" href="https://fonts.googleapis.com/css2?family=Cinzel:wght@400;500&family=Lato:wght@400;700&display=swap">
<style>
:root{
  --ink:#111;
  --header:#1b1b1b;
  --dark:#161616;
  --footer:#1d1d1d;
  --footer-bar:#101010;
  --light:#ececec;
  --news-bg:#e5e5e5;
  --card:#e6e6e6;
  --white:#fff;
  --muted:#cfcfcf;
  --text:#222;
  --rule:#555;
}
*{box-sizing:border-box;margin:0;padding:0}
html,body{width:1200px;height:2590px;overflow:hidden}
body{position:relative;font-family:"Lato",sans-serif;color:var(--text);background:var(--white)}
.abs{position:absolute}
.serif{font-family:"Cinzel",serif}

/* header */
.site-header{left:0;top:0;width:1200px;height:98px;background:var(--header)}
.brand{left:98px;top:30px;color:var(--white);font-family:"Cinzel",serif;font-size:28px;letter-spacing:.5px}
.phone{right:98px;top:14px;color:var(--white);font-family:"Cinzel",serif;font-size:18px;display:flex;align-items:center;gap:12px}
.nav{right:98px;top:64px;display:flex;gap:0;font-family:"Cinzel",serif;font-size:14px;color:var(--white)}
.nav span{padding:0 20px;border-right:1px solid #777}
.nav span:last-child{border:none;padding-right:0}

/* hero */
.hero{left:0;top:98px;width:1200px;height:515px;background:linear-gradient(115deg,#3a3a3e 0%,#1c1c22 30%,#8d8a86 55%,#c9c0b8 75%,#b58f8f 100%)}
.hero-title{left:0;top:302px;width:1200px;text-align:center;color:var(--white);font-family:"Cinzel",serif;font-size:34px;line-height:46px;letter-spacing:1px}
.hero-btn{left:493px;top:405px;width:214px;height:38px;background:var(--white);color:var(--ink);font-weight:700;font-size:15px;display:flex;align-items:center;justify-content:center;border-radius:2px}
.slide-arrow{width:38px;height:38px;border:2px solid var(--white);border-radius:50%}

/* about */
.about{left:0;top:613px;width:1200px;height:404px;background:var(--light)}
.portrait-frame{left:98px;top:665px;width:296px;height:302px;background:#d8d8d8;padding:16px}
.portrait{width:100%;height:100%;background:linear-gradient(160deg,#7d7b78,#4c4a48 60%,#2b2a2a)}
.section-title{font-family:"Cinzel",serif;color:var(--ink);font-size:33px;letter-spacing:.5px}
.title-rule{height:2px;background:linear-gradient(90deg,#222 0,#222 45%,#bbb 45%)}
.about-body{left:440px;top:722px;width:662px;font-size:13.5px;line-height:24px;color:#222}
.bullets{left:440px;top:884px;display:flex;gap:40px;font-size:14px;font-weight:700;color:var(--ink)}
.bullets span::before{content:"";display:inline-block;width:9px;height:9px;border-radius:50%;background:#333;margin-right:14px;vertical-align:1px}
.btn-dark{background:var(--ink);color:var(--white);font-size:13px;display:flex;align-items:center;justify-content:center;border-radius:2px}
.btn-outline{border:1px solid var(--white);color:var(--white);font-size:13px;display:flex;align-items:center;justify-content:center;border-radius:2px}

/* practice */
.centered{left:0;width:1200px;text-align:center}
.practice-card{top:1174px;width:309px;height:297px;background:var(--card);border-bottom:4px solid var(--ink)}
.practice-card .photo{height:142px}
.practice-icon{position:absolute;left:124px;top:116px;width:62px;height:62px;border-radius:50%;background:var(--white);display:flex;align-items:center;justify-content:center}
.practice-card h3{position:absolute;top:180px;width:100%;text-align:center;font-family:"Cinzel",serif;font-weight:500;font-size:19px;color:var(--ink)}
.practice-card p{position:absolute;top:218px;left:28px;right:28px;text-align:center;font-size:13px;line-height:19px;color:#333}

/* malta */
.malta{left:0;top:1518px;width:1200px;height:313px;background:var(--dark)}
.malta-body{left:98px;top:1620px;width:600px;font-size:13.5px;line-height:23px;color:#e4e4e4}
.malta-photo{left:775px;top:1575px;width:327px;height:190px;border:2px solid #ccc;background:linear-gradient(180deg,#2b3d6b 0%,#4a5b8a 45%,#c9823a 62%,#3a4b7d 80%,#1f2d57 100%)}

/* news */
.news{left:0;top:1831px;width:1200px;height:464px;background:var(--news-bg)}
.news-card{top:1946px;width:310px}
.news-card .photo{height:197px;position:relative}
.date-badge{position:absolute;right:16px;top:16px;width:84px;height:26px;background:#1a1a1a;color:var(--white);font-size:13px;display:flex;align-items:center;justify-content:center}
.news-card h4{margin-top:16px;font-size:15px;font-weight:700;color:var(--ink)}
.news-card p{margin-top:12px;font-size:13px;line-height:20px;color:#333}

/* footer */
.site-footer{left:0;top:2295px;width:1200px;height:252px;background:var(--footer)}
.footer-head{font-family:"Cinzel",serif;font-size:19px;color:#e8e8e8;padding-bottom:10px;border-bottom:1px solid #3a3a3a}
.quick-links{list-style:none;margin-top:18px;font-size:13px;color:#ddd;line-height:27px}
.quick-links li::before{content:"›";margin-right:10px;color:#aaa}
.contact-row{display:flex;gap:12px;font-size:13px;color:#ddd;line-height:19px;margin-top:12px;align-items:flex-start}
.map{left:568px;top:2388px;width:263px;height:137px;border:3px solid #fff;background:linear-gradient(135deg,#eef0e8,#dfe4da)}
.footer-brand{left:903px;top:2414px;font-family:"Cinzel",serif;font-size:19px;color:var(--white)}
.social{left:940px;top:2460px;display:flex;gap:8px}
.social span{width:24px;height:24px;border-radius:50%;background:#5a5a5a}
.copyright{left:0;top:2547px;width:1200px;height:43px;background:var(--footer-bar);color:#ccc;font-size:13px;display:flex;align-items:center;justify-content:center}
.vdivider{width:1px;background:#3a3a3a}
</style>
</head>
<body>

<header class="abs site-header">
  <div class="abs brand">Mercieca &amp; Falzon</div>
  <div class="abs phone">
    <svg width="28" height="28" viewBox="0 0 28 28"><circle cx="14" cy="14" r="12.5" fill="none" stroke="#fff" stroke-width="1.8"/><path d="M10 8.5l2.3-.5 1.3 3-1.5 1.2c.7 1.6 1.9 2.8 3.5 3.5l1.2-1.5 3 1.3-.5 2.3c-5 .4-9.7-4.3-9.3-9.3z" fill="#fff"/></svg>
    <span>Call: (356)-2100-4821</span>
  </div>
  <nav class="abs nav"><span>Home</span><span>About Us</span><span>Practice Areas</span><span>About Malta</span><span>Contact Us</span></nav>
</header>

<section class="abs hero" role="img" aria-label="Close-up of a passport resting on visa-stamped pages"></section>
<h1 class="abs hero-title" style="font-weight:400">The Greatest And Strongest<br>Firm You Can Trust</h1>
<div class="abs hero-btn">Request A Free Consult</div>
<svg class="abs" style="left:41px;top:335px" width="38" height="38" viewBox="0 0 38 38"><circle cx="19" cy="19" r="17.5" fill="none" stroke="#fff" stroke-width="1.6"/><path d="M22 12l-7 7 7 7" fill="none" stroke="#fff" stroke-width="1.8"/></svg>
<svg class="abs" style="left:1121px;top:335px" width="38" height="38" viewBox="0 0 38 38"><circle cx="19" cy="19" r="17.5" fill="none" stroke="#fff" stroke-width="1.6"/><path d="M16 12l7 7-7 7" fill="none" stroke="#fff" stroke-width="1.8"/></svg>

<section class="abs about"></section>
<div class="abs portrait-frame"><div class="portrait" role="img" aria-label="Portrait of a firm partner in a dark suit"></div></div>
<h2 class="abs section-title" style="left:440px;top:652px;font-weight:500">About Mercieca &amp; Falzon</h2>
<div class="abs title-rule" style="left:440px;top:704px;width:488px"></div>
<p class="abs about-body">Lorem ipsum dolor sit amet, consectetuer adipiscing elit, sed diam nonummy nibh euismod tincidunt ut laoreet dolore magna aliquam erat volutpat. Ut wisi enim ad minim veniam, quis nostrud exerci tation ullamcorper suscipit lobortis nisl ut aliquip ex ea commodo consequat. Duis autem vel eum iriure dolor in hendrerit in vulputate velit esse molestie consequat, vel illum dolore eu feugiat nulla facilisis at vero eros et accumsan et iusto odio dignissim qui blandit praesent luptatum zzril delenit augue duis dolore te feugait nulla facilisi.</p>
<div class="abs bullets"><span>Our Firms</span><span>Our Values</span></div>
<div class="abs btn-dark" style="left:440px;top:926px;width:110px;height:34px">Read More</div>

<h2 class="abs section-title centered" style="top:1053px;font-weight:500">Our Practice Areas</h2>
<div class="abs title-rule" style="left:428px;top:1104px;width:352px;background:linear-gradient(90deg,#bbb 0,#bbb 20%,#222 20%,#222 80%,#bbb 80%)"></div>
<p class="abs centered" style="top:1131px;font-size:13.5px;color:#222">Lorem ipsum dolor sit amet, consectetur adipisicing elit. Obcaecati laborum ipsa, a voluptates libero possimus sapiente.</p>
<svg class="abs" style="left:52px;top:1307px" width="20" height="36" viewBox="0 0 20 36"><path d="M17 2L3 18l14 16" fill="none" stroke="#777" stroke-width="1.6"/></svg>
<svg class="abs" style="left:1128px;top:1307px" width="20" height="36" viewBox="0 0 20 36"><path d="M3 2l14 16L3 34" fill="none" stroke="#777" stroke-width="1.6"/></svg>

<article class="abs practice-card" style="left:98px">
  <div class="photo" role="img" aria-label="Law books with a gavel and scales of justice" style="background:linear-gradient(135deg,#2a1a10,#7a5530 50%,#c9b08a)"></div>
  <div class="practice-icon"><svg width="30" height="30" viewBox="0 0 30 30"><circle cx="9" cy="17" r="6" fill="none" stroke="#111" stroke-width="2.4"/><circle cx="21" cy="17" r="6" fill="none" stroke="#111" stroke-width="2.4"/><path d="M9 11V7h12v4" fill="none" stroke="#111" stroke-width="2.2"/></svg></div>
  <h3>Crminal Law</h3>
  <p>Sed ut perspiciatis unde omnis iste natus error sit voluptatem accusantium omnis unde doloremque laudantium</p>
</article>
<article class="abs practice-card" style="left:446px">
  <div class="photo" role="img" aria-label="Passports laid on a world map" style="background:linear-gradient(135deg,#c8c2b4,#8f8a80 40%,#1f2a44 60%,#2c3553)"></div>
  <div class="practice-icon"><svg width="30" height="30" viewBox="0 0 30 30"><path d="M15 4L3 15h3v11h7v-7h4v7h7V15h3z" fill="#111"/></svg></div>
  <h3>Citizenship And Residence</h3>
  <p>Sed ut perspiciatis unde omnis iste natus error sit voluptatem accusantium omnis unde doloremque laudantium</p>
</article>
<article class="abs practice-card" style="left:793px">
  <div class="photo" role="img" aria-label="Columned courthouse facade under a blue sky" style="background:linear-gradient(180deg,#2f5aa8,#6f8fc4 45%,#d8d2c6 70%,#b8b0a2)"></div>
  <div class="practice-icon"><svg width="30" height="30" viewBox="0 0 30 30"><path d="M15 3L3 9v2h24V9z" fill="#111"/><rect x="6" y="13" width="3" height="10" fill="#111"/><rect x="11.5" y="13" width="3" height="10" fill="#111"/><rect x="16" y="13" width="3" height="10" fill="#111"/><rect x="21" y="13" width="3" height="10" fill="#111"/><rect x="3" y="24" width="24" height="3" fill="#111"/></svg></div>
  <h3>Civil Litigation</h3>
  <p>Sed ut perspiciatis unde omnis iste natus error sit voluptatem accusantium omnis unde doloremque laudantium</p>
</article>

<section class="abs malta"></section>
<h2 class="abs section-title" style="left:98px;top:1556px;color:#fff;font-weight:500">About Malta</h2>
<div class="abs title-rule" style="left:98px;top:1604px;width:230px;background:linear-gradient(90deg,#fff 0,#fff 45%,#555 45%)"></div>
<p class="abs malta-body">Lorem ipsum dolor sit amet, consectetur adipiscing elit, sed do eiusmod tempor incididunt ut labore et dolore magna aliqua. Ut enim ad minim veniam, quis nostrud exercitation ullamco laboris nisi ut aliquip ex ea commodo consequat. Duis aute irure dolor in reprehenderit in voluptate velit esse cillum dolore eu fugiat nulla pariatur. Excepteur sint occaecat cupidatat non proident, sunt in culpa qui officia deserunt mollit anim id est laborum.</p>
<div class="abs btn-outline" style="left:98px;top:1755px;width:114px;height:34px">Read More</div>
<div class="abs malta-photo" role="img" aria-label="Valletta harbour skyline lit at dusk"></div>

<section class="abs news"></section>
<h2 class="abs section-title centered" style="top:1866px;font-weight:500">Latest News</h2>
<div class="abs title-rule" style="left:492px;top:1915px;width:216px;background:linear-gradient(90deg,#bbb 0,#bbb 20%,#222 20%,#222 80%,#bbb 80%)"></div>

<article class="abs news-card" style="left:98px">
  <div class="photo" role="img" aria-label="Lawyer signing a document at a desk" style="background:linear-gradient(135deg,#2a2a2a,#4a4038 50%,#a08a6a)"><span class="date-badge">08, June</span></div>
  <h4>We denounce with righteous indignation and.</h4>
  <p>At vero eos et accusamus et iusto odio dignissimos ducimus qui blanditiis praesentium voluptatum deleniti atque corrupti quos dolores et.</p>
</article>
<article class="abs news-card" style="left:440px">
  <div class="photo" role="img" aria-label="Brass scales of justice in a courtroom" style="background:linear-gradient(135deg,#6b4424,#b07a44 50%,#e0b888)"><span class="date-badge">08, June</span></div>
  <h4>We denounce with righteous indignation and.</h4>
  <p>At vero eos et accusamus et iusto odio dignissimos ducimus qui blanditiis praesentium voluptatum deleniti atque corrupti quos dolores et.</p>
</article>
<article class="abs news-card" style="left:782px">
  <div class="photo" role="img" aria-label="White marble columns" style="background:linear-gradient(90deg,#6e6e6e,#d8d8d8 30%,#9a9a9a 50%,#e4e4e4 75%,#888)"><span class="date-badge">08, June</span></div>
  <h4>We denounce with righteous indignation and.</h4>
  <p>At vero eos et accusamus et iusto odio dignissimos ducimus qui blanditiis praesentium voluptatum deleniti atque corrupti quos dolores et.</p>
</article>

<footer class="abs site-footer">
  <div class="abs" style="left:98px;top:48px;width:160px">
    <div class="footer-head">Quick Links</div>
    <ul class="quick-links"><li>Home</li><li>About Us</li><li>Practice Areas</li><li>About Malta</li><li>Contact Us</li></ul>
  </div>
  <div class="abs vdivider" style="left:270px;top:48px;height:170px"></div>
  <div class="abs" style="left:288px;top:48px;width:200px">
    <div class="footer-head">Contact Detail</div>
    <div class="contact-row" style="margin-top:18px"><svg width="12" height="16" viewBox="0 0 12 16"><path d="M6 0a6 6 0 0 0-6 6c0 4 6 10 6 10s6-6 6-10a6 6 0 0 0-6-6zm0 8.5A2.5 2.5 0 1 1 6 3.5a2.5 2.5 0 0 1 0 5z" fill="#ddd"/></svg><span>12/4, Merchant Lane, Valletta<br>88, Orchard Street, Birkirkara</span></div>
    <div class="contact-row"><svg width="13" height="13" viewBox="0 0 13 13"><path d="M1 2l3-1 1.5 3.3-1.8 1.3a7 7 0 0 0 3.7 3.7l1.3-1.8L12 9l-1 3C5 12 1 8 1 2z" fill="#ddd"/></svg><span>(356) -2100 - 4821</span></div>
    <div class="contact-row"><svg width="14" height="13" viewBox="0 0 14 13"><rect x="3" y="0" width="8" height="4" fill="#ddd"/><rect x="0" y="4" width="14" height="6" rx="1" fill="#ddd"/><rect x="3" y="8" width="8" height="5" fill="#ddd" stroke="#1d1d1d"/></svg><span>(356) -2100 - 4822</span></div>
    <div class="contact-row"><svg width="14" height="11" viewBox="0 0 14 11"><rect width="14" height="11" fill="#ddd"/><path d="M0 0l7 6 7-6" fill="none" stroke="#1d1d1d" stroke-width="1.2"/></svg><span>info@mfadvocates.com</span></div>
  </div>
  <div class="abs vdivider" style="left:548px;top:48px;height:170px"></div>
  <div class="abs" style="left:568px;top:48px;width:263px">
    <div class="footer-head">Location Map</div>
  </div>
  <div class="abs vdivider" style="left:866px;top:48px;height:170px"></div>
</footer>
<div class="abs map" role="img" aria-label="Street map showing the office location"></div>
<svg class="abs" style="left:609px;top:2427px" width="16" height="22" viewBox="0 0 16 22"><path d="M8 0a8 8 0 0 0-8 8c0 5.5 8 14 8 14s8-8.5 8-14a8 8 0 0 0-8-8z" fill="#d9352b"/><circle cx="8" cy="8" r="3" fill="#fff"/></svg>
<div class="abs footer-brand">Mercieca &amp; Falzon</div>
<div class="abs social"><span></span><span></span><span></span><span></span></div>
<div class="abs copyright">Copyright © 2016 - Mercieca &amp; Falzon Advocates, All Rights Reserved.</div>

</body>
</html>
```